International IT business needs website revamp.

Velmor Limited would like their current website (www.velmorlimited-example.com) to be revamped/modernized to reflect up-to-date goods and services. Currently, Velmor is offering a conversational AI workflow platform for both enterprise clients and as a DIY solution for SMBs. This platform is called tqFlowbin and allows organizations to automate simple and repetitive workflows to drive their operational efficiency. In addition to the solution offering, Velmor Limited also provides professional IT services. With that said, please use www.velmorlimited-example.com and www.tqflowbin-example.ai for reference of current logos and colourways desired. Furthermore, refer to the attached PDF for a general idea of what to include in the site. The final design should be easy to navigate, clear, concise, and emphasize tqFlowbin as a solution for enterprise clients (while redirecting SMBs to the tqFlowbin website) looking to automate workflow processes/kickstart their digital transformation journey.

```html
<!DOCTYPE html>
<html lang="en">
<head>
<meta charset="utf-8">
<title>Velmor Limited</title>
<link rel="stylesheet" href="https://fonts.googleapis.com/css2?family=Poppins:wght@400;500;600;700;800&display=swap">
<style>
:root{
  --ink:#111418;
  --text:#4a4f55;
  --brand:#0a8fd6;
  --brand-dark:#0b5fae;
  --brand-light:#17c0ea;
  --pale:#edf8fd;
  --grey-band:#f4f4f4;
  --line:#dfe3e6;
  --star:#f5a623;
  --white:#fff;
}
*{box-sizing:border-box;margin:0;padding:0}
html,body{width:1200px;height:2875px;overflow:hidden;background:var(--white)}
body{position:relative;font-family:'Poppins',sans-serif;color:var(--ink)}
.abs{position:absolute}

/* hero */
.hero{left:0;top:0;width:1200px;height:564px;background:linear-gradient(100deg,#e9f3fb 0%,#cfe3f3 40%,#9fc1dc 70%,#7fa6c6 100%);clip-path:polygon(0 0,1200px 0,1200px 491px,600px 564px,0 491px)}
.brand{display:flex;align-items:center;gap:4px;font-weight:500;color:var(--ink);letter-spacing:-.5px}
.brand .sq{border:3px solid var(--ink);display:inline-block}
.header-brand{left:234px;top:28px;font-size:26px}
.header-brand .sq{width:40px;height:40px}
.nav{left:414px;top:33px;display:flex;align-items:center;gap:0;font-size:10.5px;font-weight:500;letter-spacing:.3px}
.nav a{color:var(--ink);text-decoration:none;padding:7px 12px}
.nav a.active{border:1.5px solid var(--brand);padding:6px 14px;margin-right:2px}
.phone{left:815px;top:34px;display:flex;align-items:center;gap:10px;font-size:16px;font-weight:500}
.hero-title{left:234px;top:176px;font-size:50px;line-height:53px;font-weight:700;letter-spacing:1.5px}
.hero-sub{left:234px;top:288px;width:370px;font-size:16.5px;line-height:21px;font-weight:500}
.btn{left:234px;top:377px;width:160px;height:46px;border-radius:23px;background:linear-gradient(90deg,var(--brand-light),var(--brand-dark));display:flex;align-items:center;gap:12px;padding-left:22px;color:var(--white);font-size:12.5px;font-weight:600}
.btn .sq{width:22px;height:22px;border:2px solid var(--white)}
.arrow{width:34px;height:34px;border:2px solid var(--ink)}
.dots{left:574px;top:502px;display:flex;gap:7px}
.dots i{width:12px;height:12px;border:1.5px solid var(--white);display:block}
.dots i.on{background:var(--white)}

/* section heads */
.eyebrow{width:1200px;left:0;text-align:center;color:var(--brand);font-size:12px;font-weight:600;letter-spacing:3px}
.heading{width:1200px;left:0;text-align:center;font-size:33px;font-weight:700;letter-spacing:.5px}

.services-copy{left:285px;top:714px;width:630px;text-align:center;font-size:9.3px;line-height:15px;color:var(--text)}
.hex{width:226px;height:252px;background:var(--pale);clip-path:polygon(50% 0,100% 25%,100% 75%,50% 100%,0 75%,0 25%);border-radius:18px}
.hex-icon{width:54px;height:54px;border-radius:50%;background:linear-gradient(135deg,var(--brand-light),var(--brand-dark))}
.hex-title{font-size:13px;font-weight:600;color:#2b2f33}
.hex-list{list-style:none;font-size:9.3px;line-height:15px;color:var(--text)}
.hex-list li{position:relative;padding-left:11px;margin-bottom:4px}
.hex-list li::before{content:"";position:absolute;left:0;top:5px;width:5px;height:5px;border-radius:50%;background:var(--brand)}
.center-mark{left:545px;top:907px;width:109px;height:109px;border:6px solid var(--brand);display:flex;align-items:center;justify-content:center;font-size:22px;font-weight:600;color:var(--brand)}

/* testimonials */
.testimonials{left:0;top:1159px;width:1200px;height:547px;background:var(--grey-band)}
.card{width:356px;height:291px;background:var(--white);box-shadow:0 2px 10px rgba(0,0,0,.06);padding:30px 28px}
.quote{font-size:60px;line-height:40px;font-weight:800;color:var(--brand);height:38px;font-family:Georgia,serif}
.card p{margin-top:12px;font-size:10.4px;line-height:16.3px;color:var(--text)}
.card .who{margin-top:14px;font-size:11.5px;font-weight:600;color:#2b2f33}
.stars{margin-top:6px;color:var(--star);font-size:13px;letter-spacing:1px}
.tdots{left:583px;top:1659px;display:flex;gap:6px}
.tdots i{width:5px;height:5px;border-radius:50%;background:#9aa3aa;display:block}
.tdots i.on{background:var(--brand)}

/* media */
.video{left:234px;top:1771px;width:732px;height:415px;background:linear-gradient(120deg,#5fc3ea 0%,#1f8ed0 45%,#0d5fa6 100%)}
.divider{left:600px;top:2186px;width:1px;height:287px;background:var(--line)}
.col-head{width:366px;text-align:center;font-size:26px;font-weight:700}
.names{width:366px;display:grid;grid-template-columns:1fr 1fr;row-gap:30px;text-align:center;font-size:28px;font-weight:700;color:var(--brand-dark)}
.to-top{left:582px;top:2477px;width:36px;height:36px;border-radius:50%;background:linear-gradient(135deg,var(--brand-light),var(--brand-dark))}

/* footer */
.footer{left:0;top:2500px;width:1200px;height:375px;background:var(--pale);clip-path:polygon(0 60px,600px 10px,1200px 60px,1200px 375px,0 375px)}
.footer-brand{left:234px;top:2596px;font-size:17px}
.footer-brand .sq{width:24px;height:24px;border-width:2px}
.about{left:234px;top:2636px;width:240px;font-size:9.3px;line-height:15px;color:#2b2f33}
.fcol-title{font-size:11px;font-weight:600;letter-spacing:.4px}
.fcol-title::after{content:"";display:block;width:28px;height:2px;background:var(--brand);margin-top:6px}
.flinks{list-style:none;font-size:9.3px;color:#2b2f33}
.flinks li{margin-bottom:12px}
.contact{font-size:9.3px;line-height:15px;color:#2b2f33}
.social li{display:flex;align-items:center;gap:10px;margin-bottom:9px}
.social li i{width:17px;height:17px;border-radius:50%;background:var(--brand);display:block}
.rule{left:234px;top:2808px;width:732px;height:1px;background:#d5e6ef}
.copyright{left:0;top:2838px;width:1200px;text-align:center;font-size:9.3px;color:#2b2f33}
</style>
</head>
<body>

<div class="abs hero" role="img" aria-label="Photo of two business colleagues reviewing a tablet in a bright office"></div>

<div class="abs brand header-brand"><span class="sq"></span>VELMOR</div>
<nav class="abs nav">
  <a class="active">HOME</a><a>SOLUTIONS</a><a>SERVICES</a><a>ABOUT US</a><a>CONTACT US</a>
</nav>
<div class="abs phone">
  <svg width="16" height="16" viewBox="0 0 24 24"><path fill="#0a8fd6" d="M6.6 10.8a15.1 15.1 0 0 0 6.6 6.6l2.2-2.2a1 1 0 0 1 1-.25 11.4 11.4 0 0 0 3.6.57 1 1 0 0 1 1 1V20a1 1 0 0 1-1 1A17 17 0 0 1 3 4a1 1 0 0 1 1-1h3.5a1 1 0 0 1 1 1c0 1.25.2 2.45.57 3.57a1 1 0 0 1-.25 1z"/></svg>
  (905) 555-0142
</div>

<h1 class="abs hero-title">ENTERPRISE<br>CLIENT</h1>
<p class="abs hero-sub">Velmor offers a complete turnkey solution for enterprise customers to assist in their digital transformation journey.</p>
<div class="abs btn"><span class="sq"></span>LEARN MORE</div>

<svg class="abs arrow" style="left:103px;top:288px" viewBox="0 0 34 34"><path d="M19 9l-8 8 8 8" fill="none" stroke="#111418" stroke-width="2"/></svg>
<svg class="abs arrow" style="left:1066px;top:288px" viewBox="0 0 34 34"><path d="M15 9l8 8-8 8" fill="none" stroke="#111418" stroke-width="2"/></svg>
<div class="abs dots"><i class="on"></i><i></i><i></i></div>

<!-- services -->
<div class="abs eyebrow" style="top:636px">SERVICES</div>
<h2 class="abs heading" style="top:660px">What We Do</h2>
<p class="abs services-copy">Contract Staffing: At Velmor, our staff are readily available to deliver experienced and knowledgeable assistance to fill immediate or temporary needs for a diverse range of technologies and positions. Thus, we provide seasoned IT resources with a strong sense of business acumen to bring valuable experience and expertise to our clients to achieve reduced costs, greater efficiency and better services.</p>

<svg class="abs" style="left:360px;top:775px" width="480" height="60" viewBox="0 0 480 60">
  <path d="M215 2v12q0 8-8 8H16q-8 0-8 8v28M265 2v12q0 8 8 8h191q8 0 8 8v28" fill="none" stroke="#b9c0c6" stroke-dasharray="4 3"/>
</svg>

<div class="abs hex" style="left:254px;top:837px"></div>
<div class="abs hex-icon" style="left:340px;top:869px"></div>
<div class="abs hex-title" style="left:288px;top:943px">Digital Transformation</div>
<ul class="abs hex-list" style="left:288px;top:973px;width:170px">
  <li>Process Automation via RPA and Conversational AI</li>
  <li>Enterprise Application Integration</li>
</ul>

<div class="abs center-mark">Velmor</div>

<div class="abs hex" style="left:720px;top:837px"></div>
<div class="abs hex-icon" style="left:805px;top:869px"></div>
<div class="abs hex-title" style="left:761px;top:943px">Network of Expertise</div>
<ul class="abs hex-list" style="left:754px;top:973px;width:160px">
  <li>full-stack development,</li>
  <li>from AI/ML, and data to legacy</li>
</ul>

<!-- testimonials -->
<div class="abs testimonials"></div>
<div class="abs eyebrow" style="top:1214px">TESTIMONIALS</div>
<h2 class="abs heading" style="top:1238px">What Our Clients Are Saying</h2>

<div class="abs card" style="left:234px;top:1322px">
  <div class="quote">&ldquo;</div>
  <p>“Naturally, the Passage Registry website receives thousands of visitors a day. As a result, we noticed the need to automate simple and repetitive questions to provide quick, on-demand assistance while maximizing our worker productivity without compromising costs. Thus, we enlisted Velmor Limited and their tqFlowbin solution to accomplish the task. Since launching the Passage Registry bot in Q4, 2019, we have achieved over 75% of inquiries being automatically answered successfully!”</p>
  <div class="who">Passage Registry</div>
  <div class="stars">★★★★★</div>
</div>
<div class="abs card" style="left:610px;top:1322px">
  <div class="quote">&ldquo;</div>
  <p>“Leveraging tqFlowbin’s extremely user-friendly interface, Civic Service Bureau was able to build and implement our own bot for the My Civic Account (MCA) page without the assistance of Velmor developers. By removing the need for programmers, we are able to make adjustments to our bot instantaneously!”</p>
  <div class="who">Civic Service Bureau</div>
  <div class="stars">★★★★★</div>
</div>
<div class="abs tdots"><i class="on"></i><i></i><i></i><i></i></div>

<!-- video -->
<div class="abs video" role="img" aria-label="Video still of a smiling woman working on a tablet, tinted blue"></div>
<svg class="abs" style="left:553px;top:1931px" width="94" height="94" viewBox="0 0 94 94">
  <circle cx="47" cy="47" r="44" fill="none" stroke="#fff" stroke-width="3"/>
  <path d="M38 31l26 16-26 16z" fill="#fff"/>
</svg>

<!-- clients & partners -->
<div class="abs divider"></div>
<h3 class="abs col-head" style="left:229px;top:2247px">Our Clients</h3>
<div class="abs names" style="left:229px;top:2318px"><span>Brellen</span><span>Monvar</span><span>Onyra</span><span>Cavra</span></div>
<h3 class="abs col-head" style="left:605px;top:2247px">Our Partners</h3>
<div class="abs names" style="left:605px;top:2318px"><span>Brellen</span><span>Monvar</span><span>Onyra</span><span>Cavra</span></div>

<!-- footer -->
<div class="abs footer"></div>
<svg class="abs to-top" viewBox="0 0 36 36"><path d="M12 21l6-6 6 6" fill="none" stroke="#fff" stroke-width="2"/></svg>

<div class="abs brand footer-brand"><span class="sq"></span>VELMOR</div>
<p class="abs about">Since 2011, the Velmor team has been providing professional IT services for major Canadian corporations operating in the telecommunications and financial sectors. As such, our team is highly skilled in technology integration, legacy modernization, system architecture design, application development, quality assurance, project management and more!</p>

<div class="abs fcol-title" style="left:502px;top:2595px">QUICK LINKS</div>
<ul class="abs flinks" style="left:502px;top:2638px">
  <li>Home</li><li>Solutions</li><li>Services</li><li>About Us</li><li>Contact Us</li>
</ul>

<div class="abs fcol-title" style="left:618px;top:2595px">CONTACT US</div>
<div class="abs contact" style="left:618px;top:2636px;width:200px">
  <p>1200 Example Avenue, Unit 7 &amp; 8 Markham, ON Canada, L0L 0A0</p>
  <p style="margin-top:7px">Phone: (905) 555-0142</p>
  <p style="margin-top:7px">Email: info@velmorlimited-example.com</p>
</div>

<div class="abs fcol-title" style="left:840px;top:2595px">FOLLOW US</div>
<ul class="abs flinks social" style="left:840px;top:2637px">
  <li><i></i>Friendsphere</li><li><i></i>Chirpline</li><li><i></i>ProLinkage</li>
</ul>

<div class="abs rule"></div>
<div class="abs copyright">Copyrights © 2020 Velmor Limited. All rights reserved</div>

</body>
</html>
```